Business card design needed

Family General Practitioner/ Family Physician.
Logo is the logo of the Noble Guild of Family Healers Oceania
http://kpltw.varendo.example/ImageShelf/marks/pages/NGFHO%20mark_jpg.htm
Updates

Project Deadline Extended
Reason: Just a bit more time to make changes and the weekend for me to look at things closely and to choose. Thanks, Orin

Thanks for all the submissions. So many of them are really works of art. Not one of them are not good. The ones that I am eliminating are the ones that I think are not suitable for me personally only, and because if I don't, it makes it very difficult to decide as many of you are also sending me slight variations of a card. I have just decided to choose a second place card too. Can't thank you all enough. Good luck, Orin. P.S - Working today till 10 pm as the card says :-), so probably won't be able to give a feedback till late Saturday night or Sunday morning here in Sydney, Australia. 

Project Deadline Extended
Reason: Just added a second place to the budget and realised that Australia is ahead of the rest of the world in the time zone (only :-) - don't want to offend anyone or start a debate!! ) , so Monday deadline will mean it will be a weekend for the rest of the world. Just wanted to give everyone more time to submit their best, especially since I will be picking a second card too. Can't thank everyone enough for the submissions. P.S - Not keen on photos on the card.

Industry/Entity Type

Business

Contact Information for Business Card

Dr. Orin Halvey M.B.B.S., F.N.G.F.H.O
Family General Practitioner
Address, timings, phone and fax number on the back.

Requirements
Must have
• Timings
Mon 7 am - 7 pm
Tues 7 am - 12 pm
Wed 7 am - 10 pm
Thurs 7 am - 12 pm
Fri 7 am - 8 pm
Sat 8 am - 10 pm
Sun - Off

```html
<!DOCTYPE html>
<html lang="en">
<head>
<meta charset="utf-8">
<title>Dr. Orin Halvey – Business Card</title>
<link href="https://fonts.googleapis.com/css2?family=Roboto+Condensed:wght@400;700&display=swap" rel="stylesheet">
<style>
  :root {
    --backdrop: #ece4d2;
    --card-navy: #2c4468;
    --panel-blue: #2e547f;
    --ink-sand: #c2b49a;
  }
  html, body {
    margin: 0;
    padding: 0;
    width: 1200px;
    height: 960px;
    overflow: hidden;
    background: var(--backdrop);
  }
  .card {
    position: absolute;
    left: 138px;
    top: 219px;
    width: 924px;
    height: 521px;
    border-radius: 28px;
    background: var(--card-navy);
    overflow: hidden;
    font-family: "Roboto Condensed", "Arial Narrow", sans-serif;
    color: var(--ink-sand);
  }
  .name-panel {
    position: absolute;
    left: 231px;
    top: 0;
    width: 462px;
    height: 276px;
    background: var(--panel-blue);
    border-radius: 0 0 16px 16px;
    text-align: center;
  }
  .doctor-name {
    position: absolute;
    left: 0;
    right: 0;
    top: 138px;
    margin: 0;
    font-size: 50px;
    font-weight: 700;
    line-height: 1;
    letter-spacing: 0.2px;
  }
  .credentials {
    position: absolute;
    left: 0;
    right: 0;
    top: 210px;
    margin: 0;
    font-size: 32px;
    font-weight: 400;
    line-height: 1;
    letter-spacing: 1px;
    word-spacing: 6px;
  }
  .specialty-band {
    position: absolute;
    left: 0;
    right: 0;
    top: 355px;
    height: 72px;
    background: var(--panel-blue);
    display: flex;
    align-items: center;
    justify-content: center;
  }
  .specialty {
    margin: 0;
    font-size: 36px;
    font-weight: 400;
    letter-spacing: 0.3px;
  }
</style>
</head>
<body>
  <div class="card">
    <div class="name-panel">
      <h1 class="doctor-name">Dr. Orin Halvey</h1>
      <p class="credentials">M.B.B.S., F.N.G.F.H.O.</p>
    </div>
    <div class="specialty-band">
      <p class="specialty">Family General Practitioner</p>
    </div>
  </div>
</body>
</html>
```